Brell Stone Company Business Cards

Front and Back Business Card - logo and text setup - cool design. I need workable photoshop or illustrator files so I can setup each employee card with design that is created
Updates

Hi everyone, thank you for the great entries. Please no more white and blue cards - there are so many already - black and silver only now please. thanks!

Target Market(s)

Construction Industry - Facility Managers

Industry/Entity Type

Construction

Contact Information for Business Card

I really like contemporary simplistic looks - clean neat....not opposed to seeing some black backrounds

Requirements
Must have
• Logo/website address with design on front only - www.brellstone-example.com (logo attached)
• Back:
• Name/Title/Company Address/Phone/email address
Nice to have
• Cool design
Should not have
• Nothing gimmicky like Fire or Water - since we are a Fire Protection company - it has all been done

```html
<!DOCTYPE html>
<html lang="en">
<head>
<meta charset="utf-8">
<title>Brell Stone Company Business Cards</title>
<link rel="stylesheet" href="https://fonts.googleapis.com/css2?family=Open+Sans:wght@400;600;700;800&display=swap">
<style>
  :root {
    --black: #141414;
    --black-soft: #1e1f21;
    --silver: #b8bcc2;
    --silver-light: #d9dce0;
    --silver-dark: #7d8289;
    --ink: #2a2a2a;
    --paper: #f5f5f6;
    --backdrop: #e4e5e7;
    --rule: #b4b7bb;
  }
  * { box-sizing: border-box; margin: 0; padding: 0; }
  html, body {
    width: 1200px; height: 874px; overflow: hidden;
    background: var(--backdrop);
    font-family: "Open Sans", Arial, sans-serif;
  }
  .stage { position: relative; width: 1200px; height: 874px; }
  .card {
    position: absolute; left: 320px; width: 560px; height: 320px;
    box-shadow: 0 6px 18px rgba(0,0,0,0.22);
    overflow: hidden;
  }
  .card--front { top: 97px; background: var(--black); color: var(--silver-light); }
  .card--back { top: 457px; background: var(--paper); }

  .front-brand {
    position: absolute; top: 108px; left: 0; width: 100%;
    text-align: center; font-weight: 800; font-size: 44px; letter-spacing: -0.5px;
    line-height: 1; color: var(--silver-light);
  }
  .front-url {
    position: absolute; top: 222px; left: 0; width: 100%;
    text-align: center; font-size: 13px; letter-spacing: 7px; color: var(--silver);
  }

  .back-brand {
    position: absolute; left: 34px; top: 118px; width: 220px;
    font-weight: 800; font-size: 31px; line-height: 1.05; color: var(--black);
    letter-spacing: -0.5px;
  }
  .divider {
    position: absolute; left: 282px; top: 40px; width: 1px; height: 200px;
    background: linear-gradient(to bottom, transparent, var(--rule) 25%, var(--rule) 75%, transparent);
  }
  .contact { position: absolute; left: 306px; top: 56px; color: var(--ink); }
  .contact__name { font-weight: 700; font-size: 22px; color: var(--black); line-height: 1.1; }
  .contact__title { font-size: 15px; color: var(--silver-dark); margin-bottom: 12px; }
  .contact__address { font-size: 14px; line-height: 1.35; margin-bottom: 10px; }
  .contact__list { list-style: none; font-size: 13.5px; line-height: 1.6; }
  .contact__list li { display: flex; align-items: center; gap: 8px; }
  .contact__list svg { width: 13px; height: 13px; fill: var(--black); flex: none; }

  .band { position: absolute; bottom: 0; height: 16px; }
  .band--black { left: 0; width: 62%; background: var(--black-soft); }
  .band--silver { right: 0; width: 38%; background: var(--silver); }
</style>
</head>
<body>
<div class="stage">
  <section class="card card--front">
    <div class="front-brand">Brell Stone Company</div>
    <div class="front-url">www.brellstone-example.com</div>
  </section>

  <section class="card card--back">
    <div class="back-brand">Brell Stone Company</div>
    <div class="divider"></div>
    <div class="contact">
      <div class="contact__name">Daniel Mercer</div>
      <div class="contact__title">CEO/Founder</div>
      <div class="contact__address">48 Harbor Point Road<br>Northfield, NY 11790</div>
      <ul class="contact__list">
        <li><svg viewBox="0 0 16 16" aria-hidden="true"><path d="M3.6 1.2l2.2 2.6-1.3 1.7c.9 2 2.3 3.5 4.3 4.4l1.7-1.3 2.6 2.2-1 2.6C6.7 13 3 9.3 1 3.7z"/></svg>(555) 014-2286</li>
        <li><svg viewBox="0 0 16 16" aria-hidden="true"><path d="M4 1h8v4H4zM1 6h14v7h-3v2H4v-2H1zm4 5v3h6v-3z"/></svg>(555) 014-2290</li>
        <li><svg viewBox="0 0 16 16" aria-hidden="true"><path d="M1 3h14v10H1zm1.5 1.2V5l5.5 4 5.5-4v-.8z"/></svg>info@brellstone-example.com</li>
        <li><svg viewBox="0 0 16 16" aria-hidden="true"><circle cx="8" cy="8" r="7"/></svg>www.brellstone-example.com</li>
      </ul>
    </div>
    <div class="band band--black"></div>
    <div class="band band--silver"></div>
  </section>
</div>
</body>
</html>
```